Wordpress Redesign Project

Our website needs to become amazing. Because now it's not. The homepage especially does not actively convey what we do in an elegant way. We would want a minimalist redesign of www.plovaR.com to look more like:

http://quellbytevane.com/
http://www.lumarec.com/en-us/lumarecvolta.html
http://www.vurk.com/

It needs to work on Wordpress and be easily uploaded.

We also need an inside page of case studies (currently http://www.plovar.com/social-media-clients/) that plays the video in a larger pop-up screen .

Target Market(s)

Social Media Professionals, Creative and Advertising Agencies, Event marketing professionals

Industry/Entity Type

Media

```html
<!DOCTYPE html>
<html lang="en">
<head>
<meta charset="utf-8">
<title>plovaR — Creating Brand Champions</title>
<link rel="stylesheet" href="https://fonts.googleapis.com/css2?family=Ubuntu:wght@300;400;500;700&display=swap">
<style>
:root{
  --pink:#e3177e;
  --pink-light:#f25aa5;
  --ink:#333;
  --text:#555;
  --muted:#999;
  --line:#e3e3e3;
  --footer:#3a3a3a;
  --sky:#bfe6f6;
}
*{margin:0;padding:0;box-sizing:border-box}
html,body{width:799px;height:1200px;overflow:hidden;background:#fff}
body{position:relative;font-family:"Ubuntu",sans-serif;color:var(--text)}
.abs{position:absolute}

.brand{left:53px;top:20px;display:flex;align-items:center;gap:6px}
.brand-mark{width:50px;height:51px;background:var(--pink);border-radius:11px}
.brand-name{font-size:24px;font-weight:500;color:var(--pink)}
.tagline{left:184px;top:32px;height:34px;border-left:1px solid var(--line);padding-left:12px;font-size:10px;font-weight:300;color:var(--muted);line-height:34px}

.nav{left:48px;top:86px;width:704px;height:38px;background:linear-gradient(#fafafa,#e8e8e8);border:1px solid #ddd;border-bottom:3px solid var(--pink);border-radius:4px 4px 0 0;display:flex;font-size:13px}
.nav a{display:block;padding:0 16px;line-height:36px;color:#444;text-decoration:none;border-right:1px solid #d2d2d2}
.nav a.active{background:linear-gradient(var(--pink-light),var(--pink));color:#fff;font-weight:500;padding:0 20px;border-radius:3px 0 0 0}

.hero{left:46px;top:134px;width:706px;height:242px;background:radial-gradient(ellipse at 80% 40%,#fff 0%,#e4f5fc 35%,var(--sky) 100%);border:1px solid #d7eef8;border-radius:3px}
.hero-photo{position:absolute;left:425px;top:20px;width:265px;height:200px;border-radius:50%;background:radial-gradient(#f1ece6,#d9d3cc 60%,rgba(217,211,204,0) 72%)}
.hero h1{position:absolute;left:46px;top:40px;font-size:24px;font-weight:300;color:var(--pink);line-height:28px}
.hero h1 strong{display:block;font-weight:700;font-size:26px}
.hero .lead{position:absolute;left:48px;top:100px;font-size:14px;color:#222}
.hero .sub{position:absolute;left:48px;top:122px;width:270px;font-size:8.5px;font-weight:300;color:#666;line-height:14px}
.btn{position:absolute;left:47px;top:155px;background:linear-gradient(var(--pink-light),var(--pink));color:#fff;font-size:10px;font-weight:500;padding:6px 14px;border-radius:3px}
.dots{position:absolute;left:48px;top:192px;display:flex;gap:3px}
.dots i{width:7px;height:7px;border-radius:50%;background:#111}
.dots i:first-child{background:var(--pink)}

.card{top:390px;width:168px;height:126px;border:1px solid var(--line);border-radius:3px;box-shadow:0 1px 3px rgba(0,0,0,.08);padding:12px}
.card .thumb{height:80px}
.card h3{margin-top:8px;font-size:13.5px;font-weight:400;color:var(--pink)}
.t1{background:linear-gradient(135deg,#e9c23a,#8a6b3a)}
.t2{background:linear-gradient(135deg,#b8a98c,#c07b7a)}
.t3{background:linear-gradient(135deg,#b52a2a,#5a5a5a)}
.t4{background:linear-gradient(135deg,#c9a383,#6b7fa0)}

.col{top:560px}
.col h2{font-size:16px;font-weight:400;color:#222;margin-bottom:10px}
.col p{font-size:9px;font-weight:300;line-height:15.2px;margin-bottom:7px;color:#444}
.col-sep{top:565px;width:1px;height:170px;background:var(--line)}
.posts{list-style:none}
.posts li{font-size:9px;color:var(--pink);padding:4px 0 5px 1px;border-bottom:1px solid #eee;line-height:14px}
.posts li:last-child{border:0}
.shadow{left:48px;top:752px;width:704px;height:10px;background:radial-gradient(ellipse at top,rgba(0,0,0,.07),transparent 70%)}

.feature{left:48px;top:812px;width:415px}
.feature h2{font-size:16px;font-weight:400;color:#222;line-height:20px;margin-bottom:10px}
.feature p{font-size:9px;font-weight:300;line-height:15.2px;color:#444;margin-bottom:7px}
.video{left:486px;top:808px;width:264px;height:166px;border:1px solid var(--line);padding:5px;box-shadow:0 1px 3px rgba(0,0,0,.1)}
.video .frame{position:relative;width:100%;height:100%;background:linear-gradient(110deg,#1b2240 0%,#2c2c38 45%,#0c0c0c 100%)}
.video svg{position:absolute;left:112px;top:65px}
.video .caption{position:absolute;right:8px;bottom:8px;color:#fff;text-align:right;line-height:12px}
.video .caption b{display:block;font-size:12px;font-weight:500}
.video .caption span{font-size:9px;font-weight:300}

.clients{left:70px;top:1010px;width:660px;height:60px;display:flex;align-items:center;justify-content:space-between}
.clients .name{font-size:13px;font-weight:500;color:#555;width:90px;text-align:center}

.footer{left:0;top:1082px;width:799px;height:118px;background:var(--footer)}
.footer nav{position:absolute;left:52px;top:30px;font-size:10px;color:#eee}
.footer nav span{margin:0 4px;color:#aaa}
.footer small{position:absolute;left:52px;top:52px;font-size:9px;font-weight:300;color:#999}
.social{position:absolute;left:640px;top:28px;display:flex;gap:3px}
.social i{width:24px;height:24px;border-radius:50%;background:#e8e8e8}
</style>
</head>
<body>

<header>
  <div class="abs brand"><span class="brand-mark"></span><span class="brand-name">plovaR</span></div>
  <div class="abs tagline">Creating Brand Champions</div>
  <nav class="abs nav">
    <a class="active">Home</a><a>About Us</a><a>Solutions</a><a>Resources</a><a>Our Work</a><a>Social Blog</a>
  </nav>
</header>

<section class="abs hero">
  <div class="hero-photo" role="img" aria-label="Group of smiling young people joining hands in a circle, seen from above"></div>
  <h1>Sponsor Events<strong>and Social Media KPIs</strong></h1>
  <p class="lead">Mauris vel lacus vitae vestibulum volutpat.</p>
  <p class="sub">Mauris vel lacus vitae felis vestibulum volutpat. Etiam est nunc, venenatis in, tristique eu, imperdiet ac, nisl.</p>
  <span class="btn">Reqest a Demo</span>
  <div class="dots"><i></i><i></i><i></i><i></i></div>
</section>

<section>
  <div class="abs card" style="left:48px"><div class="thumb t1" role="img" aria-label="Cheering fans in yellow at an event"></div><h3>Amplify your Event</h3></div>
  <div class="abs card" style="left:229px"><div class="thumb t2" role="img" aria-label="Young couple exploring a city square"></div><h3>Connect Venues</h3></div>
  <div class="abs card" style="left:410px"><div class="thumb t3" role="img" aria-label="Crowd waving red flags in a stadium"></div><h3>In Action</h3></div>
  <div class="abs card" style="left:590px"><div class="thumb t4" role="img" aria-label="Large diverse group of people"></div><h3>Social Solutions</h3></div>
</section>

<section>
  <div class="abs col" style="left:52px;width:215px">
    <h2>What We Do</h2>
    <p>plovaR is in the business of creating brand champi-ons. We help get consumers to put your branded content into their Friendwall News Feed and Chirpline stream while attending live events.</p>
    <p>It is product placement in social media and the most scalable form of word-of-mouth advertising. We facilitate the posts by providing a platform that connects to photobooths, roving photographers, Like boxes, games and buzz walls</p>
  </div>
  <div class="abs col-sep" style="left:278px"></div>
  <div class="abs col" style="left:299px;width:210px">
    <h2>Why Customer Choose Us</h2>
    <p>Turn live audiences into brand champions.</p>
    <p>Global consumer brands engage plovaR to leverage an asset they encounter at every event: attendees. Event guests have social network audiences who like and trust them. plovaR solutions facilitate par-ticipation and enable easy distribution of branded content to friends. Fun for guests. Amplification for brands.</p>
  </div>
  <div class="abs col-sep" style="left:520px"></div>
  <div class="abs col" style="left:542px;width:210px">
    <h2>Social Blog Post</h2>
    <ul class="posts">
      <li>What does Hallbrau do for Social Media Today?</li>
      <li>Who is using Social Media? Young? Old? Both? Yes!</li>
      <li>Social Engage Summit Interview:</li>
      <li>RFID Connects Social Media to the Real World..</li>
      <li>Adding Experiential Social Media to Events</li>
    </ul>
  </div>
  <div class="abs shadow"></div>
</section>

<section>
  <div class="abs feature">
    <h2>Veloran Amplifies Grand Circuit with RFID using<br>Social Media Technology</h2>
    <p>The video below shows how auto brands are connecting auto show and lifestyle event guests directly to social media using RFID and NFC Technology. These activations are fun for guests and expand the potential audience for social engagement beyond attendees to include their social network friends. Watch Video Below to see it in</p>
    <p>Duis tincidunt lectus quis dui viverra vestibulum. Suspendisse vulputate aliquam dui. Nulla elementum dui ut augue. Aliquam vehicula mi at mauris. Maecenas placerat, nisl at consequat rhoncus, sem nunc gravida justo, quis eleifend arcu velit quis lacus.</p>
  </div>
  <div class="abs video">
    <div class="frame" role="img" aria-label="Video still of a race car in a garage beside the speaker">
      <svg width="30" height="30" viewBox="0 0 30 30"><circle cx="15" cy="15" r="13" fill="rgba(0,0,0,.35)" stroke="#fff" stroke-width="2"/><path d="M12 9.5v11l9-5.5z" fill="#fff"/></svg>
      <div class="caption"><b>DANE HOLLOWAY</b><span>plovaR CMO</span></div>
    </div>
  </div>
</section>

<section class="abs clients">
  <svg width="14" height="24" viewBox="0 0 14 24"><path d="M12 2 2 12l10 10" fill="none" stroke="#aaa" stroke-width="1.5"/></svg>
  <span class="name">VELORAN</span>
  <span class="name">QUORRA</span>
  <span class="name">TAMSEL</span>
  <span class="name">Kizumo</span>
  <span class="name">Brambleton</span>
  <span class="name">townpicks</span>
  <svg width="14" height="24" viewBox="0 0 14 24"><path d="m2 2 10 10L2 22" fill="none" stroke="#aaa" stroke-width="1.5"/></svg>
</section>

<footer class="abs footer">
  <nav>Home<span>|</span>About Us<span>|</span>Solutions<span>|</span>Resources<span>|</span>Our Work<span>|</span>Social Blog</nav>
  <small>© 2013 Company Name. All right reserved. Term of Use</small>
  <div class="social" aria-label="Social network links"><i></i><i></i><i></i><i></i></div>
</footer>

</body>
</html>
```